Sophisticated, clean website reflecting my feminine, playful side to sell my abstract art,

I need a website no more than 3 pages to showcase my paintings, a little about me and some contact info. I do abstracts so looking for something a little edgy, yet feminine and current.
Updates

Hi there, These are some artists websites that I Iike: Marnelvoss.com (I like how airy it is) peterwallombry.com garethpolvens.com (I like how it scrolls) I'll need a place for a photo ( a headshot-i do not have it yet so I'll need to be able to upload that later) as well as an area for my bio. Also, it's important that I will be able to upload any new photos and descriptions easily so it should be user friendly. Lastly, I like in a sunny place so would like to have this seem upbeat and playful as that is how i like to paint. thanks-I'm trying to upload my photos now -

Target Market(s)

ppl ages 35-70 who want large scale art for their homes

Industry/Entity Type

art

Coding

Coded - Design and coding required

Number of Pages Required

3 page

Colors

Designer to choose colors to be used in the design.

Requirements
Must have
• photos of my art, a place for my bio, be easy to reach me. tasteful-nothing too "in your face" -my clients are pretty high end and organized. They like clean lines
Nice to have
• sophisticated background, muted tones in the back-similar clean font throughout-no cursive
Should not have
• too many dark areas. Too many blocks of color. Too serious.

```html
<!DOCTYPE html>
<html lang="en">
<head>
<meta charset="utf-8">
<title>Delia Marsh Art</title>
<link rel="stylesheet" href="https://fonts.googleapis.com/css2?family=Mulish:wght@300;400;600;700&display=swap">
<style>
:root{
  --cream:#f2e6d4;
  --blush:#f8e4d6;
  --orange:#f26a1b;
  --peach:#ec8f4e;
  --slate:#69767a;
  --ink:#1f1a17;
  --brown:#4a1d0d;
  --gold:#b57a32;
  --frame:#e3cfb0;
  --clay:#b96c55;
  --motif:#ddc6a6;
}
*{box-sizing:border-box;margin:0;padding:0}
html,body{width:1200px;height:3361px;overflow:hidden}
body{background:var(--cream);font-family:"Mulish",sans-serif;color:var(--ink);position:relative}
.abs{position:absolute}
.brand{left:143px;top:32px;width:260px;font-weight:400;font-size:34px;line-height:38px;color:var(--brown);letter-spacing:1px}
.nav{top:64px;left:454px;display:flex;gap:28px;font-size:13px;text-transform:uppercase;white-space:nowrap}
.nav span.active{border-bottom:3px solid var(--gold);padding-bottom:4px}
.search{left:856px;top:55px;width:200px;border-bottom:1px solid var(--ink);font-size:11px;padding-bottom:5px;display:flex;justify-content:space-between}
.landscape{left:0;top:420px;width:1200px;height:190px;background:linear-gradient(90deg,#8a3a1e,#c8933f 40%,#e6d3b4)}
.motif{background:var(--motif)}
.art{box-shadow:0 2px 6px rgba(0,0,0,.12)}
.hero-title{left:593px;top:172px;font-size:37px;font-weight:400;letter-spacing:.5px}
.hero-text{left:597px;top:232px;width:440px;font-size:17px;line-height:23px;color:#3b3431}
.btn{background:var(--orange);color:#fff;border-radius:24px;font-size:14px;font-weight:700;display:flex;align-items:center;justify-content:center;text-transform:uppercase}
.dots span{display:block;width:8px;height:8px;border-radius:50%;background:#6d777b;margin-bottom:11px}
.dots span.on{background:var(--orange)}
.section-title{left:0;width:1200px;text-align:center;font-size:36px;font-weight:400}
.stroke{width:100px;height:14px;left:550px}
.tile{background:#fff;padding:8px;box-shadow:0 1px 6px rgba(0,0,0,.12)}
.tile div{width:100%;height:100%}
.about{left:145px;top:2058px;width:911px;height:416px;border-radius:208px;background:var(--slate)}
.about h2{position:absolute;left:128px;top:60px;font-size:36px;font-weight:400;color:#fff}
.about p{position:absolute;left:128px;top:150px;width:340px;font-size:13.5px;line-height:24px;color:#fff;text-align:justify}
.field{background:#fff;border:1px solid #d9c6aa;border-radius:24px;font-size:14px;color:#4a423d;padding:0 25px;display:flex;align-items:center}
.footer{left:0;top:3172px;width:1200px;height:189px;background:var(--brown);color:#fff}
.footer .call{position:absolute;left:202px;top:44px;font-size:23px;font-weight:600}
.footer .fnav{position:absolute;left:524px;top:52px;display:flex;gap:28px;font-size:13px}
.footer .copy{position:absolute;left:0;width:1200px;top:104px;text-align:center;font-size:12px}
.social{position:absolute;width:36px;height:36px;border-radius:50%;border:2px solid #fff;background:var(--brown)}
</style>
</head>
<body>

<div class="abs brand">DELIA MARSH<br>ART</div>
<nav class="abs nav"><span class="active">Home</span><span>My Paintings</span><span>About Me</span><span>Contact</span></nav>
<div class="abs search"><span>SEARCH</span><svg width="11" height="11" viewBox="0 0 11 11"><circle cx="4.5" cy="4.5" r="3.3" fill="none" stroke="#1f1a17" stroke-width="1.6"/><line x1="7" y1="7" x2="10" y2="10" stroke="#1f1a17" stroke-width="1.8"/></svg></div>

<!-- hero -->
<div class="abs" style="left:42px;top:219px;width:102px;height:36px;background:var(--blush)"></div>
<div class="abs motif" style="left:74px;top:232px;width:80px;height:146px;border-radius:80px 0 0 80px" role="img" aria-label="Concentric line arc ornament"></div>
<div class="abs" style="left:1px;top:278px;width:58px;height:58px;border-radius:50%;background:var(--peach)"></div>

<div class="abs landscape" role="img" aria-label="Layered landscape of sweeping hills in rust, ochre and sand tones"></div>

<div class="abs art" style="left:143px;top:166px;width:297px;height:317px;background:linear-gradient(135deg,#5a2a20,#d9c7c6 45%,#7b3a2e)" role="img" aria-label="Abstract floral painting in burgundy and blush on white canvas"></div>
<div class="abs art" style="left:378px;top:206px;width:146px;height:224px;background:#fff;padding:8px"><div style="width:100%;height:100%;background:linear-gradient(160deg,#e9e0c8,#2f4a8a 50%,#d5a53a)" role="img" aria-label="Abstract rose painting in navy and mustard"></div></div>

<h1 class="abs hero-title">DELIA MARSH ART</h1>
<p class="abs hero-text">Lorem ipsum dolor sit amet, consectetur adipiscing elit, sed do eiusmod tempor incididunt ut labore</p>
<div class="abs btn" style="left:597px;top:308px;width:140px;height:45px">Get Started</div>
<div class="abs dots" style="left:1112px;top:235px"><span></span><span></span><span class="on"></span><span></span></div>

<!-- paintings -->
<h2 class="abs section-title" style="top:692px">MY PAINTINGS</h2>
<svg class="abs stroke" style="top:745px" viewBox="0 0 100 14"><path d="M2 8 C25 2 60 0 98 9 C60 7 30 8 2 8Z" fill="var(--gold)"/></svg>

<div class="abs" style="left:1082px;top:1037px;width:118px;height:35px;background:var(--blush)"></div>
<div class="abs motif" style="left:1114px;top:1053px;width:86px;height:140px;border-radius:86px 0 0 86px" role="img" aria-label="Concentric line arc ornament"></div>
<div class="abs" style="left:1041px;top:1094px;width:58px;height:58px;border-radius:50%;background:var(--peach)"></div>

<div class="abs tile" style="left:172px;top:806px;width:274px;height:331px"><div style="background:linear-gradient(180deg,#efece6 20%,#3b9cc4 45%,#dfe8ee)" role="img" aria-label="Blue drip abstract painting"></div></div>
<div class="abs tile" style="left:463px;top:806px;width:274px;height:331px"><div style="background:radial-gradient(circle,#b8521f,#e69f76 60%,#7f8b3a)" role="img" aria-label="Orange and olive floral abstract painting"></div></div>
<div class="abs tile" style="left:754px;top:806px;width:274px;height:331px"><div style="background:linear-gradient(180deg,#f1eeea,#9c2d22 50%,#f1eeea 80%,#c49a66)" role="img" aria-label="Red rose abstract painting on white"></div></div>
<div class="abs tile" style="left:172px;top:1165px;width:418px;height:331px"><div style="background:linear-gradient(135deg,#6d4c8e,#e7ddd3 50%,#3f2f6b)" role="img" aria-label="Purple flower burst abstract painting"></div></div>
<div class="abs tile" style="left:609px;top:1165px;width:419px;height:331px"><div style="background:linear-gradient(90deg,#8a97b4 30%,#e4ddcc 30%,#0c8c87 45%,#0c8c87 70%,#e4ddcc 70%,#1d2a66 90%)" role="img" aria-label="Vertical bands abstract painting in grey blue, teal and navy"></div></div>
<div class="abs tile" style="left:172px;top:1510px;width:274px;height:333px"><div style="background:linear-gradient(135deg,#f1ece8,#5a1f1a 50%,#d7a5a5)" role="img" aria-label="Burgundy leaf abstract painting"></div></div>
<div class="abs tile" style="left:463px;top:1510px;width:274px;height:333px"><div style="background:radial-gradient(circle,#6a2a22,#d7a3b5 50%,#f0dde1)" role="img" aria-label="Pink rose abstract painting"></div></div>
<div class="abs tile" style="left:754px;top:1510px;width:274px;height:333px"><div style="background:linear-gradient(135deg,#1a6f79,#d07a2a 50%,#2a2a2a)" role="img" aria-label="Teal and orange burst abstract painting"></div></div>

<div class="abs btn" style="left:530px;top:1907px;width:140px;height:47px">Load More</div>

<!-- about -->
<div class="abs" style="left:0;top:1992px;width:158px;height:35px;background:var(--blush)"></div>
<div class="abs motif" style="left:0;top:2008px;width:126px;height:144px;border-radius:0 72px 72px 0" role="img" aria-label="Concentric line arc ornament"></div>
<div class="abs" style="left:141px;top:2050px;width:58px;height:58px;border-radius:50%;background:var(--peach)"></div>

<section class="abs about">
  <h2>ABOUT ME</h2>
  <svg style="position:absolute;left:128px;top:110px" width="100" height="14" viewBox="0 0 100 14"><path d="M2 8 C25 2 60 0 98 9 C60 7 30 8 2 8Z" fill="var(--gold)"/></svg>
  <p>Lorem ipsum dolor sit amet, consectetur adipiscing elit, sed do eiusmod tempor incididunt ut labore et dolore magna aliqua. Quis ipsum suspendisse ultrices gravida. Risus commodo viverra maecenas accumsan lacus vel facorem ipsum dolor sit amet, consectetur adipiscing elit, sed do eiusmod tempor</p>
  <div class="btn" style="position:absolute;left:128px;top:318px;width:140px;height:46px">Read More</div>
</section>
<div class="abs" style="left:668px;top:2089px;width:352px;height:352px;border-radius:50%;background:var(--orange)"></div>
<div class="abs" style="left:656px;top:2093px;width:350px;height:350px;border-radius:50%;background:var(--slate)"></div>
<div class="abs" style="left:657px;top:2093px;width:348px;height:348px;border-radius:50%;background:radial-gradient(circle at 50% 40%,#d9b89a,#6b7a92 70%,#3e4550)" role="img" aria-label="Portrait photo of the artist holding a brush and palette"></div>
<svg class="abs" style="left:980px;top:2088px" width="70" height="60" viewBox="0 0 70 60">
  <circle cx="35" cy="12" r="12" fill="var(--ink)"/>
  <path d="M0 26 H70 A35 35 0 0 1 0 26Z" fill="var(--clay)"/>
</svg>

<!-- contact -->
<div class="abs" style="left:1096px;top:2517px;width:104px;height:36px;background:var(--blush)"></div>
<div class="abs motif" style="left:1128px;top:2530px;width:72px;height:143px;border-radius:72px 0 0 72px" role="img" aria-label="Concentric line arc ornament"></div>
<div class="abs" style="left:1055px;top:2574px;width:58px;height:58px;border-radius:50%;background:var(--peach)"></div>

<svg class="abs" style="left:144px;top:2604px" width="912" height="478" viewBox="0 0 912 478">
  <path d="M277 2 H2 V476 H910 V2 H635" fill="none" stroke="var(--frame)" stroke-width="3"/>
</svg>
<h2 class="abs section-title" style="top:2573px">CONTACT US</h2>
<svg class="abs stroke" style="top:2627px" viewBox="0 0 100 14"><path d="M2 8 C25 2 60 0 98 9 C60 7 30 8 2 8Z" fill="var(--gold)"/></svg>

<div class="abs field" style="left:213px;top:2696px;width:251px;height:47px">Enter Name</div>
<div class="abs field" style="left:474px;top:2696px;width:251px;height:47px">Enter Email</div>
<div class="abs field" style="left:734px;top:2696px;width:252px;height:47px">Phone</div>
<div class="abs field" style="left:213px;top:2755px;width:251px;height:47px">Address</div>
<div class="abs field" style="left:474px;top:2755px;width:251px;height:47px">City</div>
<div class="abs field" style="left:734px;top:2755px;width:252px;height:47px">Zipcode</div>
<div class="abs field" style="left:213px;top:2815px;width:773px;height:102px;align-items:flex-start;padding-top:14px">Message</div>
<div class="abs btn" style="left:530px;top:2943px;width:140px;height:47px">Submit</div>

<svg class="abs" style="left:110px;top:3040px" width="70" height="66" viewBox="0 0 70 66">
  <circle cx="35" cy="12" r="12" fill="var(--ink)"/>
  <path d="M0 28 H70 A35 35 0 0 1 0 28Z" fill="var(--clay)"/>
</svg>

<!-- footer -->
<footer class="abs footer">
  <svg style="position:absolute;left:145px;top:37px" width="44" height="44" viewBox="0 0 44 44">
    <circle cx="22" cy="22" r="20" fill="none" stroke="var(--gold)" stroke-width="2.5"/>
    <path d="M15 12 l5 0 2 6 -3 2 c1 3 3 5 6 6 l2-3 6 2 0 5 c-10 1-19-8-18-18z" fill="var(--gold)"/>
  </svg>
  <div class="call">Call Us : +1 888 888 8888</div>
  <div class="fnav"><span>HOME</span><span>MY PAINTINGS</span><span>ABOUT ME</span><span>CONTACT</span></div>
  <div class="social" style="left:933px;top:42px"></div>
  <div class="social" style="left:975px;top:42px"></div>
  <div class="social" style="left:1018px;top:42px"></div>
  <div class="copy">© 2022 Delia Marsh Art. All rights reserved.Privacy &nbsp;|&nbsp; Terms of Use</div>
</footer>

</body>
</html>
```